International Clinical Software Company needs a new business card design

We are looking for a new business card design for our company that has recently expanded into the UK market, making us a multinational company.
After having rebranded our website and produced a new style guide, we are looking for a business card that is creative and attention grabbing, while being consistent with the style and colour scheme used on the new website, www.plumvora.example
We produce care management technology for the aged care market, but the main aspect we aim to communicate is the human element of our software, and the way it assists in providing better care for aged people, and stronger relationships between aged people and the staff that care for them.
Our current business card is a dark green with gold text, which makes the text quite difficult to read, not very aesthetically appealing and the colour scheme looks quite dated.
We would like something fresh and modern, that can still be colourful but doesn't use large blocks of dark colour, and uses the colours within our logo.
Something tying in with the leaves that are used in our logo could work quite nicely, along with the Autumn/Fall colours of soft greens, yellows and reds (also in our existing logo). However also happy to look at fresh, completely out of the box ideas we may not have yet considered.
Target Market(s)
The people that receive this business card work in the aged card or health industry and are either corporate/management level staff or clinical (Registered Nurses, care workers etc.)
Industry/Entity Type
Health Product
Contact Information for Business Card
Company Name - BrindlewayCare
Company locations: United Kingdom, Australia, New Zealand
Staff Details:
Staff name: Derek Mallow
Staff job title: Executive Chairman
Staff email: d.mallow@plumvora.example
Office phone number: 01742 918576
Font styles to use
Other font styles liked:
- Calibri
Requirements
Must have
- Must include the BrindlewayCare brand name in it's current font
- Must include logo (3 leaves in gold circle)
- Must include Business Card Details
Nice to have
- Elements of gold
- White space
- Something autumn themed but not too cliched
Should not have
- No blue - used by a major competitor and we would like to differentiate from them
- Large blocks of dark green colour (the green that appears in our leaves on the logo on our current business card is the background colour and it is far too dark)

```html
<!DOCTYPE html>
<html lang="en">
<head>
<meta charset="utf-8">
<title>BrindlewayCare – Business Card</title>
<link href="https://fonts.googleapis.com/css2?family=Arimo:wght@400;700&display=swap" rel="stylesheet">
<style>
  :root {
    --page-bg: #e6e4e0;
    --card-white: #ffffff;
    --gold: #c1aa82;
    --gold-text: #b59d74;
    --accent-red: #c8174c;
    --panel-text: #ffffff;
    --shadow: rgba(0, 0, 0, 0.12);
  }
  * { box-sizing: border-box; margin: 0; padding: 0; }
  html, body {
    width: 1200px;
    height: 950px;
    overflow: hidden;
    background: var(--page-bg);
    font-family: "Arimo", Arial, sans-serif;
  }
  .stage {
    width: 1200px;
    height: 950px;
    display: flex;
    align-items: center;
    justify-content: center;
  }
  .business-card {
    width: 900px;
    height: 580px;
    display: flex;
    background: var(--card-white);
    box-shadow: 0 10px 30px var(--shadow);
  }
  .contact-panel {
    width: 360px;
    height: 100%;
    background: var(--gold);
    border-right: 4px solid var(--accent-red);
    color: var(--panel-text);
    padding: 200px 0 0 44px;
  }
  .person-name {
    font-weight: 700;
    font-size: 30px;
    line-height: 1.1;
  }
  .person-title {
    font-size: 19px;
    margin-top: 6px;
  }
  .locations {
    font-size: 19px;
    line-height: 1.3;
    margin-top: 34px;
  }
  .contact-list {
    list-style: none;
    margin-top: 14px;
    font-size: 19px;
  }
  .contact-list li {
    display: flex;
    align-items: center;
    gap: 12px;
    line-height: 1.45;
  }
  .contact-list svg {
    width: 18px;
    height: 18px;
    flex: none;
    fill: var(--panel-text);
  }
  .brand-panel {
    flex: 1;
    display: flex;
    flex-direction: column;
    align-items: center;
    justify-content: center;
    gap: 26px;
  }
  .brand-dot {
    width: 120px;
    height: 120px;
    border-radius: 50%;
    background: var(--gold);
  }
  .brand-name {
    font-size: 52px;
    font-weight: 400;
    color: var(--gold-text);
    letter-spacing: 0.5px;
  }
</style>
</head>
<body>
<main class="stage">
  <article class="business-card">
    <section class="contact-panel">
      <h1 class="person-name">Derek Mallow</h1>
      <p class="person-title">Executive Chairman</p>
      <p class="locations">United Kingdom,<br>Australia, New Zealand</p>
      <ul class="contact-list">
        <li>
          <svg viewBox="0 0 20 20" aria-hidden="true"><path d="M3 7c0-2 3-4 7-4s7 2 7 4l-3 1-1-2H7L6 8 3 7zM5 9h10l2 8H3z"/></svg>
          <span>01742 918576</span>
        </li>
        <li>
          <svg viewBox="0 0 20 20" aria-hidden="true"><path d="M2 5h16v10H2z M2 5l8 6 8-6" stroke="#c1aa82" stroke-width="1.5"/></svg>
          <span>d.mallow@plumvora.example</span>
        </li>
        <li>
          <svg viewBox="0 0 20 20" aria-hidden="true"><circle cx="10" cy="10" r="8"/><path d="M6 10h8M10 6l4 4-4 4" stroke="#c1aa82" stroke-width="2" fill="none"/></svg>
          <span>www.plumvora.example</span>
        </li>
      </ul>
    </section>
    <section class="brand-panel">
      <div class="brand-dot" aria-hidden="true"></div>
      <p class="brand-name">BrindlewayCare</p>
    </section>
  </article>
</main>
</body>
</html>
```